Business card for medical clinic

I need an upmarket, modern medical/health business card for my clinic

Contact Information for Business Card

name, address, email, qr code

```html
<!DOCTYPE html>
<html lang="en">
<head>
<meta charset="utf-8">
<title>Meridian Care Clinic – Business Card</title>
<link href="https://fonts.googleapis.com/css2?family=Montserrat:wght@400;500;600;700&display=swap" rel="stylesheet">
<style>
  :root{
    --bg:#e9ebef;
    --card:#ffffff;
    --navy:#1f2a48;
    --sky:#29a8e0;
    --brand:#1f6fa6;
    --ink:#1d2230;
    --rule:#29a8e0;
  }
  *{margin:0;padding:0;box-sizing:border-box}
  html,body{width:1200px;height:900px;overflow:hidden;background:var(--bg)}
  body{font-family:"Montserrat",sans-serif;color:var(--ink);position:relative}
  .card{
    position:absolute;left:300px;width:600px;height:343px;
    background:var(--card);overflow:hidden;
    box-shadow:0 10px 28px rgba(20,30,50,.18);
  }
  .card--front{top:70px}
  .card--back{top:487px}
  .card__bands{position:absolute;left:0;bottom:0;width:600px;height:40px}
  .brand{display:flex;align-items:center;gap:14px;position:absolute}
  .brand__dot{border-radius:50%;border:3px solid var(--sky);flex:none}
  .brand__name{font-weight:600;color:var(--brand);letter-spacing:.06em;text-transform:uppercase;white-space:nowrap}
  .card--front .brand{left:150px;top:128px}
  .card--front .brand__dot{width:52px;height:52px}
  .card--front .brand__name{font-size:26px}
  .card--back .brand{left:46px;top:176px}
  .card--back .brand__dot{width:30px;height:30px;border-width:2px}
  .card--back .brand__name{font-size:15px}
  .divider{position:absolute;left:300px;top:70px;width:1px;height:190px;background:var(--rule)}
  .contact{position:absolute;left:326px;top:62px}
  .contact__name{font-size:22px;font-weight:700;color:var(--brand);line-height:1.1}
  .contact__role{font-size:11px;font-weight:500;margin-top:3px}
  .contact__address{font-size:11px;font-weight:500;line-height:1.4;margin-top:16px}
  .contact__list{list-style:none;margin-top:14px}
  .contact__item{display:flex;align-items:center;gap:9px;font-size:11px;font-weight:500;line-height:1;margin-bottom:9px}
  .contact__icon{width:12px;height:12px;flex:none}
</style>
</head>
<body>

<section class="card card--front">
  <div class="brand">
    <span class="brand__dot"></span>
    <span class="brand__name">Meridian Care Clinic</span>
  </div>
  <svg class="card__bands" viewBox="0 0 600 40" aria-hidden="true">
    <polygon points="0,28 360,28 370,40 0,40" fill="var(--navy)"/>
    <polygon points="368,6 600,6 600,40 382,40" fill="var(--sky)"/>
    <polygon points="362,16 372,16 392,40 382,40" fill="#ffffff"/>
  </svg>
</section>

<section class="card card--back">
  <div class="brand">
    <span class="brand__dot"></span>
    <span class="brand__name">Meridian Care Clinic</span>
  </div>
  <div class="divider"></div>
  <div class="contact">
    <p class="contact__name">Daniel Hart</p>
    <p class="contact__role">Managing Director</p>
    <p class="contact__address">240 Cedar Grove Lane<br>Ridgeland, MS 39157</p>
    <ul class="contact__list">
      <li class="contact__item">
        <svg class="contact__icon" viewBox="0 0 12 12" aria-hidden="true"><path d="M3 1 L5 3.5 L4 5 Q5 7 7 8 L8.5 7 L11 9 L9.5 11 Q5 11 1 3 Z" fill="var(--sky)"/></svg>
        555.210.4478
      </li>
      <li class="contact__item">
        <svg class="contact__icon" viewBox="0 0 12 12" aria-hidden="true"><rect x="0.5" y="2.5" width="11" height="7.5" rx="1" fill="var(--sky)"/><path d="M1 3 L6 7 L11 3" stroke="#fff" stroke-width="1" fill="none"/></svg>
        hello@meridiancare.com
      </li>
      <li class="contact__item">
        <svg class="contact__icon" viewBox="0 0 12 12" aria-hidden="true"><circle cx="6" cy="6" r="5.5" fill="var(--sky)"/><path d="M0.5 6 H11.5 M6 0.5 Q3 6 6 11.5 M6 0.5 Q9 6 6 11.5" stroke="#fff" stroke-width=".8" fill="none"/></svg>
        www.meridiancare.com
      </li>
    </ul>
  </div>
  <svg class="card__bands" viewBox="0 0 600 40" aria-hidden="true">
    <polygon points="0,28 360,28 370,40 0,40" fill="var(--navy)"/>
    <polygon points="368,6 600,6 600,40 382,40" fill="var(--sky)"/>
    <polygon points="362,16 372,16 392,40 382,40" fill="#ffffff"/>
  </svg>
</section>

</body>
</html>
```